Hvac and insulation company needs good looking business card design

We are hvac and insulation company and looking for a new business cards that look to today standards designs

Target Market(s)

homeowners

Industry/Entity Type

Hvac

Contact Information for Business Card

Name: Walter Brinoku
Home comfort consultant
address: 4827 Dunmore St #215 Oakland, CA 94619
office: 888-316-2790
cell: 510-742-3185
Lic.# 584261
Email: walter@corvane-hvac.com
Web: corvane-hvac.com

Requirements
Must have
• clean and sleek look
Nice to have
• simple with a clean look
Should not have
• to busy business card

```html
<!DOCTYPE html>
<html lang="en">
<head>
<meta charset="utf-8">
<title>Corvane Home Solutions – Business Card</title>
<link href="https://fonts.googleapis.com/css2?family=Lato:wght@400;700&display=swap" rel="stylesheet">
<style>
  :root {
    --page-bg: #e9ecef;
    --card-white: #ffffff;
    --card-grey: #7f7f7f;
    --brand-orange: #f28a1e;
    --text-grey: #5c5c5c;
    --text-white: #ffffff;
  }
  * { box-sizing: border-box; margin: 0; padding: 0; }
  html, body {
    width: 1200px; height: 1000px; overflow: hidden;
    background: var(--page-bg);
    font-family: 'Lato', Arial, sans-serif;
  }
  .canvas { position: relative; width: 1200px; height: 1000px; }
  .card {
    position: absolute; left: 250px; width: 700px; height: 396px;
    box-shadow: 0 6px 18px rgba(0,0,0,0.18);
  }
  .card-front { top: 74px; background: var(--card-white); }
  .card-back { top: 530px; background: var(--card-grey); color: var(--text-white); }

  .wordmark { position: absolute; display: flex; align-items: center; gap: 16px; }
  .wordmark-square { width: 62px; height: 62px; background: var(--brand-orange); }
  .wordmark-text { display: flex; flex-direction: column; }
  .wordmark-name { font-weight: 700; font-size: 68px; line-height: 1; color: var(--brand-orange); }
  .wordmark-tag { font-size: 21px; letter-spacing: 4px; color: var(--text-grey); margin-left: 4px; margin-top: 2px; }

  .card-front .wordmark { left: 50%; top: 150px; transform: translateX(-50%); }
  .front-web {
    position: absolute; left: 0; right: 0; bottom: 24px;
    text-align: center; font-size: 20px; color: var(--text-grey);
  }

  .card-back .wordmark { right: 30px; top: 70px; gap: 12px; }
  .card-back .wordmark-square { width: 44px; height: 44px; background: var(--text-white); }
  .card-back .wordmark-name { font-size: 48px; color: var(--text-white); }
  .card-back .wordmark-tag { font-size: 15px; letter-spacing: 3px; color: var(--text-white); }

  .person { position: absolute; left: 35px; top: 115px; }
  .person-name { font-size: 39px; line-height: 1.1; }
  .person-role { font-size: 21px; margin-top: 2px; }
  .divider { position: absolute; left: 33px; right: 30px; top: 197px; height: 2px; background: rgba(255,255,255,0.85); }
  .address {
    position: absolute; right: 30px; top: 207px;
    font-size: 18.5px; line-height: 1.4; text-align: right;
  }
  .contacts { position: absolute; left: 35px; top: 248px; list-style: none; }
  .contacts li { display: flex; align-items: center; gap: 14px; font-size: 25px; height: 36px; }
  .contacts li.email { font-size: 24px; height: 30px; margin-top: 0; }
  .contacts svg { width: 20px; height: 20px; fill: var(--text-white); flex: none; }
  .license { position: absolute; right: 30px; top: 352px; font-size: 18.5px; }
</style>
</head>
<body>
<main class="canvas">
  <section class="card card-front" aria-label="Card front">
    <div class="wordmark">
      <span class="wordmark-square"></span>
      <span class="wordmark-text">
        <span class="wordmark-name">corvane</span>
        <span class="wordmark-tag">home solutions</span>
      </span>
    </div>
    <p class="front-web">www.corvane-hvac.com</p>
  </section>

  <section class="card card-back" aria-label="Card back">
    <div class="person">
      <h1 class="person-name">Walter Brinoku</h1>
      <p class="person-role">Home comfort consultant</p>
    </div>
    <div class="wordmark">
      <span class="wordmark-square"></span>
      <span class="wordmark-text">
        <span class="wordmark-name">corvane</span>
        <span class="wordmark-tag">home solutions</span>
      </span>
    </div>
    <div class="divider"></div>
    <p class="address">4827 Dunmore St #215 Oakland,<br>CA 94619</p>
    <ul class="contacts">
      <li class="office">
        <svg viewBox="0 0 20 20" aria-hidden="true"><path d="M2 7c0-3 4-4 8-4s8 1 8 4v2h-4V7.5H6V9H2z"/><path d="M5 10h10l2 7H3z"/><circle cx="10" cy="13.5" r="2" fill="#7f7f7f"/></svg>
        <span>888-316-2790</span>
      </li>
      <li class="cell">
        <svg viewBox="0 0 20 20" aria-hidden="true"><path d="M4 2l3 0 2 4-2 2c1 2 3 4 5 5l2-2 4 2v3c0 1-1 2-2 2C9 18 2 11 2 4c0-1 1-2 2-2z"/></svg>
        <span>510-742-3185</span>
      </li>
      <li class="email">
        <svg viewBox="0 0 20 20" aria-hidden="true"><path d="M2 5h16v11H2z M3 6l7 5 7-5" fill="none" stroke="#fff" stroke-width="1.6"/></svg>
        <span>walter@corvane-hvac.com</span>
      </li>
    </ul>
    <p class="license">Lic.# 584261</p>
  </section>
</main>
</body>
</html>
```